Cleaning Service Company In need of Good Web presence.

The company is a cleaning service company which provides professional staff and service for cleaning. This is a project to build a site that is both solid and a strong recognition of our organization. It is supposed to show quality, cleanliness, professionalism. The use of images and art for imagery is all good just to have a site that is consistent and solid. There might be a chance to make stationary, logo and business cars if someone feels they can build a brand that is consistent. The image we are going for is clean solid and to stand out. Finally stationary should not be expensive to print.

Current logo is attached and can be used or can be made more creative.

Target Market(s)

Corporate and Government entities, that will feel that this company has a brand that sets it apart from the rest. The company is new so the modification of the logo will not be an issue if a more solid brand come out of this project. The idea is to have a clean consistent product that stands our from others in terms of website, stationary, etc

Industry/Entity Type

Cleaning Service

Contact Information for Business Card

P.O.Box 51947
Riffa
Kingdom of Bahrain

Logo Text

Harbor Lane Services

Number of Pages Required

4 page

Font styles to use
Sans Serif

Colors
abd036
cadf82
eaf2ce
9bcb3b

Requirements
Must have
• Green Color to be used in order to stick to the name. Also the creativity and boldness in an elegant manner.
Nice to have
• Arabic name of company
• هاربر لين سرفسس ذ.م.م
• if cannot be put at least make a location should be chosen
• Also could be a bit of 3D given to the logo if it could stay elegent.
Should not have
• Should not show people cleaning.

```html
<!DOCTYPE html>
<html lang="en">
<head>
<meta charset="utf-8">
<title>Harbor Lane Services</title>
<link rel="stylesheet" href="https://fonts.googleapis.com/css2?family=Montserrat:wght@400;500;600;700&family=Open+Sans:wght@400;600;700&display=swap">
<style>
:root{
  --lime:#9bcb3b;
  --lime-deep:#8dc63f;
  --forest:#0b6b3a;
  --ink:#222;
  --body:#3a3a3a;
  --mist:#ebebeb;
  --panel:#f3f1f1;
  --night:#252525;
  --white:#fff;
}
*{margin:0;padding:0;box-sizing:border-box}
html,body{width:1200px;height:2786px;overflow:hidden}
body{position:relative;background:var(--white);font-family:"Open Sans",Arial,sans-serif;color:var(--body)}
.abs{position:absolute}
.heading{font-family:"Montserrat",Arial,sans-serif}

/* header */
.site-header{left:0;top:0;width:1200px;height:143px;background:var(--white)}
.brand{left:98px;top:30px;display:flex;align-items:center;gap:12px}
.brand-dot{width:30px;height:30px;border-radius:50%;background:var(--lime)}
.brand-name{font-family:"Montserrat",Arial,sans-serif;font-weight:700;font-size:17px;color:var(--forest);line-height:1.15;width:130px}
.arabic-name{left:440px;top:36px;font-size:13px;color:#444;direction:rtl}
.top-contact{top:28px;display:flex;align-items:center;gap:10px;font-size:16px;font-weight:600}
.top-contact .ico{width:36px;height:36px;border-radius:50%;border:2px solid currentColor;display:flex;align-items:center;justify-content:center}
.top-mail{left:590px;color:var(--ink)}
.top-call{left:916px;color:var(--lime)}
.main-nav{left:328px;top:90px;display:flex;gap:0;font-family:"Montserrat",Arial,sans-serif;font-weight:500;font-size:15px;color:var(--ink)}
.main-nav a{display:block;padding:0 18px;height:36px;line-height:36px;color:inherit;text-decoration:none;margin-right:18px}
.main-nav a.active{background:var(--lime);color:var(--white);padding:0 15px;margin-right:20px}

/* hero */
.hero{left:0;top:143px;width:1200px;height:497px;background:linear-gradient(90deg,#8c98a3 0%,#aab4bc 40%,#9aa5ae 62%,#3d4c5c 72%,#5d6a77 100%)}
.hero-title{left:98px;top:232px;font-family:"Montserrat",Arial,sans-serif;font-weight:700;font-size:46px;color:var(--white)}
.hero-text{left:98px;top:320px;width:520px;font-size:15.5px;line-height:28px;color:var(--white);font-weight:600}
.hero-btn{left:98px;top:412px;width:126px;height:52px;border:2px solid var(--white);background:var(--lime);color:var(--white);font-size:14px;font-weight:600;text-align:center;line-height:48px}
.hero-dots{left:98px;top:496px;display:flex;gap:4px}
.hero-dots span{width:13px;height:13px;border-radius:50%;border:2px solid var(--white)}
.hero-dots span.on{border-color:var(--lime)}
.hero-swoop{left:0;top:600px}

/* info strip */
.info-box{top:598px;height:115px;background:var(--lime);color:var(--white);display:flex;align-items:flex-start;padding:28px 0 0 20px;gap:16px}
.info-office{left:98px;width:335px}
.info-mail{left:767px;width:335px}
.info-box h3{font-family:"Montserrat",Arial,sans-serif;font-size:22px;font-weight:600;margin-bottom:10px}
.info-box p{font-size:13.5px}
.call-box{left:433px;top:598px;width:334px}
.call-text{left:433px;top:665px;width:334px;text-align:center;color:var(--white)}
.call-text h3{font-family:"Montserrat",Arial,sans-serif;font-size:22px;font-weight:600}
.call-text p{font-size:16px;margin-top:8px}

/* about */
.section-title{font-family:"Montserrat",Arial,sans-serif;font-weight:600;color:var(--lime);text-align:center;left:0;width:1200px}
.rule{height:2px;background:var(--lime)}
.about-title{top:808px;font-size:26px}
.about-rule{left:528px;top:864px;width:144px}
.about-copy{left:130px;top:900px;width:940px;text-align:center;font-size:13px;line-height:23px}
.about-copy p{margin-bottom:14px}
.btn{top:1066px;height:46px;font-size:14px;font-weight:600;text-align:center;line-height:42px;border:2px solid}
.btn-solid{left:472px;width:120px;background:var(--forest);border-color:var(--forest);color:var(--white)}
.btn-line{left:608px;width:122px;border-color:var(--ink);color:var(--ink);border-width:2px}

/* services */
.services{left:0;top:1185px;width:1200px;height:588px;background:var(--mist)}
.services-title{top:1244px;font-size:26px;line-height:38px}
.services-rule{left:528px;top:1338px;width:144px}
.service-photo{top:1398px;width:325px;height:249px}
.ph-building{left:98px;background:linear-gradient(160deg,#6c8fa6,#2a3948 70%,#1a232c)}
.ph-office{left:438px;background:linear-gradient(170deg,#7a7a76,#d7d6d2 55%,#f1f0ee)}
.ph-window{left:776px;background:linear-gradient(120deg,#3a3b36,#b9c4b8 45%,#eef2ee 75%,#c8ccc6)}
.service-name{top:1678px;width:325px;text-align:center;font-family:"Montserrat",Arial,sans-serif;font-weight:600;font-size:18px;color:var(--forest)}

/* why */
.why-panel{left:380px;top:1862px;width:721px;height:441px;background:var(--panel)}
.why-person{left:46px;top:1848px;width:622px;height:455px;background:radial-gradient(ellipse at 35% 55%,#ffffff 0%,#f1efec 45%,rgba(243,241,241,0) 75%)}
.why-title{left:468px;top:1900px;font-family:"Montserrat",Arial,sans-serif;font-weight:600;font-size:26px;color:var(--lime)}
.why-rule{left:468px;top:1949px;width:145px}
.why-copy{left:468px;top:1978px;width:590px;font-size:13px;line-height:23px}
.why-copy p{margin-bottom:14px}

/* footer */
.site-footer{left:0;top:2303px;width:1200px;height:483px;background:var(--night)}
.footer-brand{left:0;width:1200px;top:2400px;display:flex;justify-content:center;align-items:center;gap:12px}
.footer-brand .brand-name{color:var(--lime);width:auto}
.social{left:0;width:1200px;top:2532px;display:flex;justify-content:center;gap:8px}
.social span{width:40px;height:40px;border-radius:50%;border:2px solid var(--white)}
.footer-nav{left:0;width:1200px;top:2632px;display:flex;justify-content:center;font-family:"Montserrat",Arial,sans-serif;font-weight:600;font-size:15px;color:var(--white)}
.footer-nav span{padding:0 28px;position:relative}
.footer-nav span+span::before{content:"|";position:absolute;left:-3px}
.footer-rule{left:98px;top:2702px;width:1003px;height:1px;background:var(--white)}
.copyright{left:0;width:1200px;top:2738px;text-align:center;font-size:13px;font-weight:700;color:var(--white)}
</style>
</head>
<body>

<header class="site-header abs">
  <div class="brand abs"><span class="brand-dot"></span><span class="brand-name">Harbor Lane Services</span></div>
  <div class="arabic-name abs">هاربر لين سرفسس ذ.م.م</div>
  <div class="top-contact top-mail abs">
    <span class="ico"><svg width="18" height="14" viewBox="0 0 18 14"><rect x="1" y="1" width="16" height="12" fill="none" stroke="#222" stroke-width="1.6"/><path d="M1 1l8 7 8-7" fill="none" stroke="#222" stroke-width="1.6"/></svg></span>
    Mail: info@harborlaneservices.com
  </div>
  <div class="top-contact top-call abs">
    <span class="ico"><svg width="16" height="16" viewBox="0 0 16 16"><path d="M3 1.5l3 3-1.7 2a9 9 0 0 0 5.2 5.2l2-1.7 3 3-2 2C6.5 14.5 1.5 9.5 1 3.5z" fill="none" stroke="#9bcb3b" stroke-width="1.5"/></svg></span>
    Call: 180 047 3915
  </div>
  <nav class="main-nav abs">
    <a class="active" href="#">Home</a><a href="#">About</a><a href="#">Our Service</a><a href="#">Why Choose Us</a><a href="#">Areas we work</a><a href="#" style="margin-right:0">Contact Us</a>
  </nav>
</header>

<section class="hero abs" role="img" aria-label="City skyline with a glass office tower"></section>
<h1 class="hero-title abs">HARBOR LANE SERVICES</h1>
<p class="hero-text abs">Nemo enim ipsam voluptatem quia voluptas sit aspernatur aut odit aut fugit, sed quia consequuntur.</p>
<div class="hero-btn abs">READ MORE</div>
<div class="hero-dots abs"><span class="on"></span><span></span><span></span><span></span><span></span></div>
<svg class="hero-swoop abs" width="1200" height="60" viewBox="0 0 1200 60"><path d="M0 40 Q 40 30 98 10 L98 60 L0 60Z" fill="#fff"/><path d="M0 40 Q 40 30 98 10" stroke="#9bcb3b" stroke-width="4" fill="none"/><path d="M1200 40 Q 1160 30 1102 10 L1102 60 L1200 60Z" fill="#fff"/><path d="M1200 40 Q 1160 30 1102 10" stroke="#9bcb3b" stroke-width="4" fill="none"/></svg>

<div class="info-box info-office abs">
  <svg width="34" height="52" viewBox="0 0 34 52"><path d="M17 2a14 14 0 0 1 14 14c0 11-14 26-14 26S3 27 3 16A14 14 0 0 1 17 2z" fill="none" stroke="#fff" stroke-width="3"/><circle cx="17" cy="16" r="5" fill="none" stroke="#fff" stroke-width="3"/><path d="M3 49h28" stroke="#fff" stroke-width="3"/></svg>
  <div><h3>VISIT OUR OFFICE</h3><p>27 Cedar Court Road, Bahrain</p></div>
</div>
<svg class="call-box abs" width="334" height="150" viewBox="0 0 334 150"><path d="M0 0H334V115L167 150L0 115Z" fill="#0b6b3a"/><rect x="159" y="20" width="18" height="32" rx="3" fill="none" stroke="#fff" stroke-width="2.5"/><circle cx="168" cy="46" r="1.8" fill="#fff"/></svg>
<div class="call-text abs"><h3>CALL US NOW</h3><p>180 047 3915</p></div>
<div class="info-box info-mail abs">
  <svg width="46" height="32" viewBox="0 0 46 32" style="margin-top:14px"><rect x="2" y="2" width="42" height="28" fill="none" stroke="#fff" stroke-width="3"/><path d="M2 2l21 17L44 2" fill="none" stroke="#fff" stroke-width="3"/></svg>
  <div><h3>DROP A MESSAGE</h3><p>info@harborlaneservices.com</p></div>
</div>

<h2 class="section-title about-title abs">ABOUT HARBOR LANE SERVICES</h2>
<div class="rule about-rule abs"></div>
<div class="about-copy abs">
  <p>Sed ut perspiciatis unde omnis iste natus error sit voluptatem accusantium doloremque laudantium, totam rem aperiam, eaque ipsa quae ab illo inventore veritatis et quasi architecto beatae vitae dicta sunt explicabo.</p>
  <p>Nemo enim ipsam voluptatem quia voluptas sit aspernatur aut odit aut fugit, sed quia consequuntur magni dolores eos qui ratione voluptatem sequi nesciunt. Neque porro quisquam est, qui dolorem ipsum quia dolor sit amet, consectetur, adipisci velit, sed quia non numquam eius modi tempora incidunt ut labore et dolore magnam aliquam quaerat voluptatem.</p>
</div>
<div class="btn btn-solid abs">READ MORE</div>
<div class="btn btn-line abs">CONTACT US</div>

<section class="services abs"></section>
<h2 class="section-title services-title abs">HIGH QUALITY CLEANING SERVICES<br>AND AFFORDABLE PRICES</h2>
<div class="rule services-rule abs"></div>
<div class="service-photo ph-building abs" role="img" aria-label="Glass facade of a tall building against the sky"></div>
<div class="service-photo ph-office abs" role="img" aria-label="Polished marble office floor"></div>
<div class="service-photo ph-window abs" role="img" aria-label="Bright window with a view of trees"></div>
<div class="service-name abs" style="left:98px">BUILDING CLEANING</div>
<div class="service-name abs" style="left:438px">OFFICE CLEANING</div>
<div class="service-name abs" style="left:776px">WINDOW CLEANING</div>

<div class="why-panel abs"></div>
<div class="why-person abs" role="img" aria-label="Company representative in white traditional dress gesturing to the text"></div>
<h2 class="why-title abs">WHY HARBOR LANE SERVICES</h2>
<div class="rule why-rule abs"></div>
<div class="why-copy abs">
  <p>Nemo enim ipsam voluptatem quia voluptas sit aspernatur aut odit aut fugit, sed quia consequuntur magni dolores eos qui ratione voluptatem sequi nesciunt. Neque porro quisquam est, qui dolorem ipsum quia dolor sit amet, consectetur, adipisci velit.</p>
  <p>Aspernatur aut odit aut fugit, sed quia consequuntur magni dolores eos qui ratione voluptatem sequi nesciunt. Neque porro quisquam est, qui dolorem ipsum quia dolor sit amet, consectetur, adipisci velit, sed quia non numquam eius modi tempora incidunt.</p>
</div>

<footer class="site-footer abs"></footer>
<div class="footer-brand abs"><span class="brand-dot"></span><span class="brand-name">Harbor Lane Services</span></div>
<div class="social abs"><span></span><span></span><span></span><span></span><span></span></div>
<nav class="footer-nav abs"><span>HOME</span><span>PROFILE</span><span>OUR SERVICE</span><span>WHY CHOOSE US</span><span>AREAS WE WORK</span><span>CONTACT US</span></nav>
<div class="footer-rule abs"></div>
<div class="copyright abs">Copyright © 2017 Harbor Lane Services. All Right Reserved</div>

</body>
</html>
```